Tovel & Associates - London New Letting and Property Management Company *

Tovel & Associates LTD is a new company based in London, and works with brand new residential property in the city centre.

We are aiming to have 1000 new properties a year.

We are looking for something modern and minimalistic :
Logo ,Monogram, Paper Head and Business Card.

Target Market(s)

Internation landlords

Industry/Entity Type

Real Estate

Logo Text

Tovel & Associates

Colors

Designer to choose colors to be used in the design.

Requirements
Nice to have
• A particular monogram with "TA"
Should not have
• Little House over the logo

```html
<!DOCTYPE html>
<html lang="en">
<head>
<meta charset="utf-8">
<title>Tovel &amp; Associates — Business Card</title>
<link rel="stylesheet" href="https://fonts.googleapis.com/css2?family=Montserrat:wght@400;500;600;700&display=swap">
<style>
  :root {
    --backdrop: #2b2624;
    --card-blue: #1c4f87;
    --card-blue-deep: #173f6e;
    --accent-blue: #2c9fe0;
    --ink-white: #ffffff;
  }
  * { box-sizing: border-box; margin: 0; padding: 0; }
  html, body {
    width: 1200px; height: 715px; overflow: hidden;
    background: var(--backdrop);
    font-family: "Montserrat", sans-serif;
  }
  .stage {
    position: relative; width: 1200px; height: 715px;
    display: flex; align-items: center; justify-content: center; gap: 50px;
  }
  .card {
    position: relative; width: 525px; height: 300px;
    background: linear-gradient(160deg, var(--card-blue) 0%, var(--card-blue-deep) 100%);
    color: var(--ink-white);
  }

  /* Lockup: square, name, rules flanking LTD */
  .lockup {
    display: flex; flex-direction: column; align-items: center;
    width: max-content;
  }
  .lockup-square { background: var(--ink-white); }
  .lockup-name {
    font-weight: 600; color: var(--ink-white);
    white-space: nowrap; letter-spacing: 0.01em; line-height: 1.1;
  }
  .lockup-suffix-row {
    display: flex; align-items: center; width: 100%;
  }
  .lockup-rule { flex: 1; height: 2px; background: var(--accent-blue); }
  .lockup-suffix {
    color: var(--accent-blue); font-weight: 500; letter-spacing: 0.08em;
  }

  .card-front { display: flex; align-items: center; justify-content: center; }
  .card-front .lockup-square { width: 46px; height: 46px; margin-bottom: 14px; }
  .card-front .lockup-name { font-size: 32px; }
  .card-front .lockup-suffix-row { margin-top: 8px; gap: 14px; }
  .card-front .lockup-suffix { font-size: 17px; }

  .card-back .lockup {
    position: absolute; left: 150px; top: 150px; transform: translate(-50%, -50%);
  }
  .card-back .lockup-square { width: 34px; height: 34px; margin-bottom: 10px; }
  .card-back .lockup-name { font-size: 22px; }
  .card-back .lockup-suffix-row { margin-top: 6px; gap: 10px; }
  .card-back .lockup-suffix { font-size: 12px; }

  .divider {
    position: absolute; left: 292px; top: 58px; width: 2px; height: 190px;
    background: var(--accent-blue);
  }
  .contact { position: absolute; left: 312px; top: 62px; }
  .contact-name {
    font-weight: 700; font-size: 18px; color: var(--accent-blue);
    text-transform: uppercase; letter-spacing: 0.02em;
  }
  .contact-role { font-size: 13px; color: var(--accent-blue); margin-bottom: 12px; }
  .contact-list { list-style: none; font-size: 13px; line-height: 20px; }
  .contact-list li { display: flex; align-items: center; gap: 8px; }
  .contact-list svg { width: 11px; height: 11px; flex: none; }
  .web-domain { color: var(--accent-blue); }
  .address { font-size: 13px; line-height: 20px; margin-top: 8px; }
</style>
</head>
<body>
<main class="stage">
  <section class="card card-front">
    <div class="lockup">
      <span class="lockup-square"></span>
      <span class="lockup-name">Tovel &amp; Associates</span>
      <div class="lockup-suffix-row">
        <span class="lockup-rule"></span>
        <span class="lockup-suffix">LTD</span>
        <span class="lockup-rule"></span>
      </div>
    </div>
  </section>

  <section class="card card-back">
    <div class="lockup">
      <span class="lockup-square"></span>
      <span class="lockup-name">Tovel &amp; Associates</span>
      <div class="lockup-suffix-row">
        <span class="lockup-rule"></span>
        <span class="lockup-suffix">LTD</span>
        <span class="lockup-rule"></span>
      </div>
    </div>
    <div class="divider"></div>
    <div class="contact">
      <p class="contact-name">Elena Hart</p>
      <p class="contact-role">Founder</p>
      <ul class="contact-list">
        <li>
          <svg viewBox="0 0 12 12" fill="none" stroke="#ffffff" stroke-width="1.2"><rect x="3" y="0.8" width="6" height="10.4" rx="1"/><line x1="5" y1="9.4" x2="7" y2="9.4"/></svg>
          020. 7946. 0381
        </li>
        <li>
          <svg viewBox="0 0 12 12" fill="#ffffff"><path d="M2.5 1 L4.6 1 L5.4 3.6 L4.1 4.6 C4.8 6 6 7.2 7.4 7.9 L8.4 6.6 L11 7.4 L11 9.5 C11 10.3 10.3 11 9.5 11 C5 11 1 7 1 2.5 C1 1.7 1.7 1 2.5 1 Z"/></svg>
          020. 7946. 0522
        </li>
        <li>
          <svg viewBox="0 0 12 12" fill="none" stroke="#ffffff" stroke-width="1.2"><rect x="0.8" y="2.4" width="10.4" height="7.2"/><polyline points="0.8,2.4 6,6.6 11.2,2.4"/></svg>
          info@tovelassociates.co.uk
        </li>
        <li>
          <svg viewBox="0 0 12 12" fill="none" stroke="#ffffff" stroke-width="1.1"><circle cx="6" cy="6" r="5"/><ellipse cx="6" cy="6" rx="2.2" ry="5"/><line x1="1" y1="6" x2="11" y2="6"/></svg>
          <span>www.<span class="web-domain">tovelassociates</span>.co.uk</span>
        </li>
      </ul>
      <p class="address">48 Harlow Crescent<br>London, EC2A 4QN</p>
    </div>
  </section>
</main>
</body>
</html>
```